Redesign Website - Current one too plain

The description is in the uploaded file. Please let me know if you need any more information. I'd prefer it if someone could implement the design to a WordPress site but the best design will win, regardless.
I would like the forms to look nice as well
UPDATE:
I don't think we can use the images that I provided, I think they make the site look a bit 'cheap' and I really don't know how to replace them. One thought I have had is to make the "Simple, Unique, Effective" a second feature on the right side of the page with the search on the left
Target Market(s)
Small companies, private sellers of cars and people who rent their caravan/holiday home out
Industry/Entity Type
Advertising
Number of Pages Required
3 page
Colors
Designer to choose colors to be used in the design.
Look and feel
Each slider illustrates characteristics of the customer's brand and the style your logo design should communicate.

```html
<!DOCTYPE html>
<html lang="en">
<head>
<meta charset="utf-8">
<title>BLOTZ – Find adverts by code</title>
<link href="https://fonts.googleapis.com/css2?family=Open+Sans:wght@400;600;700&display=swap" rel="stylesheet">
<style>
:root{
  --lime:#e2ff00;
  --lime-pale:#f7fbdc;
  --ink:#111111;
  --text:#333333;
  --grey-band:#efefef;
  --white:#ffffff;
  --footer:#222222;
  --star:#f5c33b;
}
*{box-sizing:border-box;margin:0;padding:0}
html,body{width:1200px;height:2248px;overflow:hidden}
body{font-family:"Open Sans",Arial,sans-serif;color:var(--text);background:var(--white);position:relative}
.abs{position:absolute}
.nowrap{white-space:nowrap}
.mark{background:linear-gradient(transparent 72%,var(--lime) 72%);padding:0 6px}
.brand{display:flex;align-items:center;gap:10px;font-size:21px;font-weight:400;color:var(--ink)}
.brand-dot{width:60px;height:60px;border-radius:50%;background:var(--ink)}
.nav{display:flex;gap:24px;font-size:15px;color:var(--ink)}
.site-header{top:0;left:0;width:1200px;height:108px}
.site-header .brand{position:absolute;left:112px;top:22px}
.site-header .nav{position:absolute;right:111px;top:46px}
.hero{top:108px;left:0;width:1200px;height:472px;background:var(--grey-band);overflow:hidden}
.hero-welcome{left:112px;top:110px;font-size:26px;color:var(--ink);display:flex;align-items:flex-end;gap:14px}
.hero-welcome .big{font-size:62px;line-height:1;background:linear-gradient(transparent 80%,var(--lime) 80%);padding:0 8px}
.hero-lead{left:112px;top:187px;width:385px;font-size:15px;line-height:29px}
.finder{left:112px;top:263px;width:305px;height:65px;background:#e3e3e3;border-radius:8px;display:flex;gap:10px;padding:7px}
.finder .field{background:var(--white);border-radius:6px;height:51px;display:flex;align-items:center;justify-content:space-between;padding:0 14px;font-size:19px;color:var(--ink)}
.finder svg{width:10px;height:16px}
.btn{background:var(--lime);color:var(--ink);border-radius:7px;font-size:16px;display:flex;align-items:center;justify-content:center;gap:6px}
.search-btn{left:112px;top:342px;width:114px;height:41px}
.hero-photo{left:506px;top:49px;width:694px;height:428px;border-radius:40px 0 0 0;background:linear-gradient(135deg,#d6d6d6,#a8a8a8 60%,#8f8f8f)}
.section-title{left:0;width:1200px;text-align:center;font-size:42px;font-weight:600;color:var(--ink)}
.about-bar{left:113px;top:705px;width:86px;height:330px;background:var(--lime)}
.about-photo{left:54px;top:755px;width:461px;height:212px;border-radius:60px 90px 20px 10px;background:linear-gradient(180deg,#f4f4f4,#d4d4d4)}
.about-text{left:569px;top:712px;width:532px}
.about-text .lead{font-size:15px;line-height:28px;color:var(--ink);font-weight:500;margin-bottom:13px}
.about-text p{font-size:15px;line-height:28.5px}
.about-text .learn-btn{width:118px;height:41px;margin-top:22px}
.why{top:1082px;left:0;width:1200px;height:517px;background:var(--grey-band)}
.card{background:var(--white);border-radius:6px;text-align:center;box-shadow:0 2px 10px rgba(0,0,0,.04)}
.feature{top:1251px;width:280px;height:264px}
.feature .icon{width:74px;height:74px;border-radius:50%;background:var(--lime-pale);margin:38px auto 0}
.feature h3{font-size:19px;font-weight:700;color:var(--ink);margin-top:16px}
.feature p{font-size:15.5px;line-height:28px;margin-top:12px;padding:0 22px}
.review{top:1791px;width:468px;height:271px;text-align:left}
.review .avatar{position:absolute;left:23px;top:29px;width:102px;height:102px;border-radius:50%;background:linear-gradient(160deg,#e6e6e6,#4a5060);border:1px solid #222}
.review .quote{position:absolute;left:38px;top:140px;font-family:Georgia,serif;font-size:130px;line-height:1;color:#eef9a0}
.review .name{position:absolute;left:149px;top:31px;font-size:19px;color:var(--ink)}
.review .meta{position:absolute;left:149px;top:64px;display:flex;align-items:center;gap:16px;font-size:10px;color:#666}
.review .source{display:flex;align-items:center;gap:5px}
.review .source i{width:13px;height:13px;border-radius:50%;background:#9bb0d0;display:block}
.review .stars{display:flex;gap:2px}
.review .stars svg{width:14px;height:14px}
.review p{position:absolute;left:149px;top:96px;width:300px;font-size:15.5px;line-height:28.5px}
.site-footer{top:2121px;left:0;width:1200px;height:127px;background:var(--footer)}
.site-footer .brand{position:absolute;left:112px;top:26px;color:var(--lime)}
.site-footer .brand-dot{background:var(--lime)}
.site-footer .nav{position:absolute;right:110px;top:36px;color:var(--white)}
.site-footer .copy{position:absolute;right:110px;top:73px;color:var(--white);font-size:15px}
</style>
</head>
<body>

<header class="abs site-header">
  <div class="brand"><span class="brand-dot"></span>BLOTZ</div>
  <nav class="nav"><span>Home</span><span>Advertise</span><span>Contact</span><span>Register</span><span>Login</span></nav>
</header>

<section class="abs hero">
  <div class="abs hero-welcome">Welcome to <span class="big">BLOTZ</span></div>
  <p class="abs hero-lead">Lorem ipsum dolor sit amet, consectetur adipiscing elit, sed do eiusmod tempor incididunt ut labore.</p>
  <div class="abs finder">
    <div class="field" style="width:66px">A <svg viewBox="0 0 10 16"><path d="M1 6 5 1 9 6Z M1 10 5 15 9 10Z" fill="#999"/></svg></div>
    <div class="field" style="width:66px">1 <svg viewBox="0 0 10 16"><path d="M1 6 5 1 9 6Z M1 10 5 15 9 10Z" fill="#999"/></svg></div>
    <div class="field" style="width:134px">caravan <svg viewBox="0 0 10 16"><path d="M1 6 5 1 9 6Z M1 10 5 15 9 10Z" fill="#999"/></svg></div>
  </div>
  <div class="abs btn search-btn"><svg width="13" height="13" viewBox="0 0 13 13"><circle cx="5.5" cy="5.5" r="4.3" fill="none" stroke="#111" stroke-width="1.4"/><path d="M8.7 8.7 12 12" stroke="#111" stroke-width="1.4"/></svg>search</div>
  <div class="abs hero-photo" role="img" aria-label="Photo of a static caravan, a work van and an SUV, each tagged with a yellow code label"></div>
</section>

<h2 class="abs section-title" style="top:616px">ABOUT <span class="mark">US</span></h2>
<div class="abs about-bar"></div>
<div class="abs about-photo" role="img" aria-label="Photo of a white motorhome with a yellow code label"></div>
<div class="abs about-text">
  <div class="lead">Lorem ipsum dolor sit amet, consectetur adipiscilt, sed do eiusmod tempor incididunt ut labodolore magna iqua.</div>
  <p>Sed ut perspiciatis unde omnis iste natus error sit voltatem accusantium doloremque laudantium, totam rem aperiam, psa quae ab illo inventore veritatis et quasi architecto beatae vitae dictaunt explicabo. Nemo enim ipsam voluptatem quia voluptas sit aspernatur aut odit aut fgit, sed quia consequuntur magni dolores eos qui ratione voluptatem.</p>
  <div class="btn learn-btn">Learn More</div>
</div>

<section class="abs why"></section>
<h2 class="abs section-title" style="top:1138px">WHY <span class="mark">US</span></h2>
<div class="abs card feature" style="left:112px"><div class="icon" role="img" aria-label="Icon of a hand tapping an easy button"></div><h3>Simple</h3><p>create your advert and display your code</p></div>
<div class="abs card feature" style="left:460px"><div class="icon" role="img" aria-label="Icon of a gear with a star"></div><h3>Unique</h3><p>customers find you by an <span class="nowrap">easy-to-remember</span> code</p></div>
<div class="abs card feature" style="left:808px"><div class="icon" role="img" aria-label="Icon of a thumbs up"></div><h3>Effective</h3><p>customers are directed to you &amp; not a list of your competitors</p></div>

<h2 class="abs section-title" style="top:1678px">CLIENT <span class="mark">REVIEWS</span></h2>

<article class="abs card review" style="left:113px">
  <div class="avatar" role="img" aria-label="Portrait photo of the reviewer"></div>
  <div class="quote">“</div>
  <div class="name">Dana K</div>
  <div class="meta"><span class="source"><i></i>Revu review</span>
    <span class="stars"><svg viewBox="0 0 10 10"><path d="M5 .5 6.3 3.6 9.6 3.8 7.1 6 7.9 9.3 5 7.5 2.1 9.3 2.9 6 .4 3.8 3.7 3.6Z" fill="#f5c33b"/></svg><svg viewBox="0 0 10 10"><path d="M5 .5 6.3 3.6 9.6 3.8 7.1 6 7.9 9.3 5 7.5 2.1 9.3 2.9 6 .4 3.8 3.7 3.6Z" fill="#f5c33b"/></svg><svg viewBox="0 0 10 10"><path d="M5 .5 6.3 3.6 9.6 3.8 7.1 6 7.9 9.3 5 7.5 2.1 9.3 2.9 6 .4 3.8 3.7 3.6Z" fill="#f5c33b"/></svg><svg viewBox="0 0 10 10"><path d="M5 .5 6.3 3.6 9.6 3.8 7.1 6 7.9 9.3 5 7.5 2.1 9.3 2.9 6 .4 3.8 3.7 3.6Z" fill="#f5c33b"/></svg><svg viewBox="0 0 10 10"><path d="M5 .5 6.3 3.6 9.6 3.8 7.1 6 7.9 9.3 5 7.5 2.1 9.3 2.9 6 .4 3.8 3.7 3.6Z" fill="#f5c33b"/></svg></span></div>
  <p>Sed ut perspiciatis unde oms iste natus error sit voltatem acctium doloremque laudantium, totam rem aperiam, psa quae ab illo inventore veritatis et quasi architecto beatae vitae &nbsp;»</p>
</article>

<article class="abs card review" style="left:619px">
  <div class="avatar" role="img" aria-label="Portrait photo of the reviewer"></div>
  <div class="quote">“</div>
  <div class="name">Dana K</div>
  <div class="meta"><span class="source"><i></i>Revu review</span>
    <span class="stars"><svg viewBox="0 0 10 10"><path d="M5 .5 6.3 3.6 9.6 3.8 7.1 6 7.9 9.3 5 7.5 2.1 9.3 2.9 6 .4 3.8 3.7 3.6Z" fill="#f5c33b"/></svg><svg viewBox="0 0 10 10"><path d="M5 .5 6.3 3.6 9.6 3.8 7.1 6 7.9 9.3 5 7.5 2.1 9.3 2.9 6 .4 3.8 3.7 3.6Z" fill="#f5c33b"/></svg><svg viewBox="0 0 10 10"><path d="M5 .5 6.3 3.6 9.6 3.8 7.1 6 7.9 9.3 5 7.5 2.1 9.3 2.9 6 .4 3.8 3.7 3.6Z" fill="#f5c33b"/></svg><svg viewBox="0 0 10 10"><path d="M5 .5 6.3 3.6 9.6 3.8 7.1 6 7.9 9.3 5 7.5 2.1 9.3 2.9 6 .4 3.8 3.7 3.6Z" fill="#f5c33b"/></svg><svg viewBox="0 0 10 10"><path d="M5 .5 6.3 3.6 9.6 3.8 7.1 6 7.9 9.3 5 7.5 2.1 9.3 2.9 6 .4 3.8 3.7 3.6Z" fill="#f5c33b"/></svg></span></div>
  <p>Sed ut perspiciatis unde oms iste natus error sit voltatem acctium doloremque laudantium, totam rem aperiam, psa quae ab illo inventore veritatis et quasi architecto beatae vitae &nbsp;»</p>
</article>

<footer class="abs site-footer">
  <div class="brand"><span class="brand-dot"></span>BLOTZ</div>
  <nav class="nav"><span>Home</span><span>Advertise</span><span>Contact</span><span>Register</span><span>Login</span></nav>
  <div class="copy">2023 Blotz. All Rights Reserved.</div>
</footer>

</body>
</html>
```